Agriculture Business Card

I want to use my existing logo and use my tagline of "Don't Guess...Soil Test" on the card. Looking for a double sided card that will really get peoples attention.
Contact Info:
Marlow Field Crop Edge
Calvin Brusk
2917 K Lane
Larkin, NE 68593
402-555-0193
calvin.r.brusk@fieldmailbox.net

```html
<!DOCTYPE html>
<html lang="en">
<head>
<meta charset="utf-8">
<title>Marlow Field Crop Edge – Business Card</title>
<link href="https://fonts.googleapis.com/css2?family=Oswald:wght@400;500;600&display=swap" rel="stylesheet">
<style>
  :root {
    --backdrop: #d2d2d2;
    --card-light: #ececec;
    --soil-dark: #4a2c2f;
    --grain-gold: #e1a213;
    --leaf-green: #5fac3c;
    --brand-rose: #9b5f58;
    --ink: #333333;
    --paper-text: #ebe6e6;
  }
  * { box-sizing: border-box; margin: 0; padding: 0; }
  html, body { width: 1200px; height: 1101px; overflow: hidden; }
  body {
    background: var(--backdrop);
    font-family: "Oswald", sans-serif;
    position: relative;
  }
  .card {
    position: absolute;
    top: 266px;
    width: 303px;
    height: 534px;
    overflow: hidden;
  }
  .card--front { left: 246px; background: var(--card-light); text-align: center; }
  .card--back { left: 641px; background: var(--soil-dark); }

  .brand-mark {
    position: absolute; left: 50%; top: 46px;
    width: 70px; height: 70px; margin-left: -35px;
    border-radius: 50%; background: var(--grain-gold);
  }
  .brand-name {
    position: absolute; left: 0; right: 0; top: 150px;
    color: var(--brand-rose);
    font-weight: 500; font-size: 20px; line-height: 24px;
  }
  .person-name {
    position: absolute; left: 0; right: 0; top: 236px;
    color: var(--ink); font-weight: 600; font-size: 36px; letter-spacing: 0.5px;
  }
  .divider {
    position: absolute; left: 50%; width: 66px; margin-left: -33px;
    height: 2px; background: var(--grain-gold); border-radius: 1px;
  }
  .divider--upper { top: 305px; }
  .divider--lower { top: 417px; }
  .icon-row {
    position: absolute; left: 0; right: 0; top: 330px;
    display: flex; justify-content: center; gap: 8px;
  }
  .icon { width: 19px; height: 19px; }
  .icon--pin { position: absolute; left: 50%; margin-left: -10px; top: 439px; }
  .contact-line {
    position: absolute; left: 0; right: 0;
    color: var(--ink); font-weight: 500; font-size: 14px; line-height: 18px;
  }
  .contact-line--phone { top: 356px; }
  .contact-line--email { top: 376px; font-size: 13px; }
  .contact-line--address { top: 465px; }

  .tagline {
    position: absolute; left: 0; right: 0; top: 52px;
    color: var(--paper-text); text-align: center;
    font-weight: 500; font-size: 40px; line-height: 55px;
  }
  .back-brand {
    position: absolute; left: 0; right: 0; top: 240px;
    color: var(--leaf-green); text-align: center;
    font-weight: 500; font-size: 20px; line-height: 24px;
  }
  .soil-layers {
    position: absolute; left: 0; right: 0; bottom: 0; height: 216px;
    background: linear-gradient(180deg, #b9861c 0%, var(--grain-gold) 45%, #d49a14 100%);
  }
</style>
</head>
<body>
  <section class="card card--front">
    <div class="brand-mark"></div>
    <p class="brand-name">Marlow Field Crop Edge</p>
    <h1 class="person-name">CALVIN BRUSK</h1>
    <div class="divider divider--upper"></div>
    <div class="icon-row">
      <svg class="icon icon--phone" viewBox="0 0 20 20" aria-hidden="true">
        <circle cx="10" cy="10" r="10" fill="#9b5f58"/>
        <path d="M7 5.5c.6-.4 1.2-.2 1.5.4l.8 1.6c.2.5.1 1-.3 1.3l-.6.4c.5 1.2 1.3 2 2.4 2.6l.5-.6c.3-.4.9-.5 1.3-.2l1.5 1c.5.3.6 1 .2 1.4l-.8.9c-.6.6-1.5.7-2.2.3-2.3-1.2-4-3-5-5.4-.3-.8-.1-1.6.5-2.1z" fill="#fff"/>
      </svg>
      <svg class="icon icon--mail" viewBox="0 0 20 20" aria-hidden="true">
        <circle cx="10" cy="10" r="10" fill="#9b5f58"/>
        <rect x="5" y="6.5" width="10" height="7" rx="1" fill="#fff"/>
        <path d="M5.5 7l4.5 3.5L14.5 7" stroke="#9b5f58" stroke-width="1" fill="none"/>
      </svg>
    </div>
    <p class="contact-line contact-line--phone">402-555-0193</p>
    <p class="contact-line contact-line--email">calvin.r.brusk@fieldmailbox.net</p>
    <div class="divider divider--lower"></div>
    <svg class="icon icon--pin" viewBox="0 0 20 20" aria-hidden="true">
      <circle cx="10" cy="10" r="10" fill="#9b5f58"/>
      <path d="M10 4.5a3.6 3.6 0 0 0-3.6 3.6c0 2.6 3.6 6.9 3.6 6.9s3.6-4.3 3.6-6.9A3.6 3.6 0 0 0 10 4.5z" fill="#fff"/>
      <circle cx="10" cy="8.2" r="1.4" fill="#9b5f58"/>
    </svg>
    <p class="contact-line contact-line--address">2917 K Lane Larkin, NE 68593</p>
  </section>

  <section class="card card--back">
    <h2 class="tagline">Don't Guess...<br>Soil Test</h2>
    <p class="back-brand">Marlow Field<br>Crop Edge</p>
    <div class="soil-layers" role="img" aria-label="Illustrated soil layers of golden clods and stones beneath the surface"></div>
  </section>
</body>
</html>
```